TalkHarbor - Language Coaching Services

Sleek, innovative, trendy design for Language Coaching business.

TalkHarbor is a new UK based company that provides Language Coaching services. We offer highly personalized on-line and face to face language courses. We also impart learning techniques workshops based on the latest neuroscience research for second-language acquisition.

Target Market(s)

See attached info

Industry/Entity Type

Consulting

Contact Information for Business Card

TalkHarbor
DaniaKV@talkharbor.co.uk
TalkHarbor.co.uk
London, UK

Font styles to use
Sans Serif

```html
<!DOCTYPE html>
<html lang="en">
<head>
<meta charset="utf-8">
<title>TalkHarbor Business Card</title>
<link href="https://fonts.googleapis.com/css2?family=Lato:wght@300;400;700&display=swap" rel="stylesheet">
<style>
  :root {
    --page-bg: #2a2a2c;
    --card-bg: #1c1d1f;
    --card-back-bg: #202123;
    --brand-blue: #1a9ad6;
    --text-light: #f2f2f2;
    --rule: #6b6d70;
    --pattern-tone-a: #27282a;
    --pattern-tone-b: #1f2022;
  }
  * { box-sizing: border-box; margin: 0; padding: 0; }
  html, body {
    width: 1200px; height: 1108px; overflow: hidden;
    background: var(--page-bg);
    font-family: "Lato", sans-serif;
  }
  .canvas {
    position: relative; width: 1200px; height: 1108px;
    display: flex; justify-content: center; align-items: center; gap: 70px;
  }
  .card {
    position: relative; width: 440px; height: 700px;
    border-radius: 26px; overflow: hidden;
  }
  .card--front {
    background: var(--card-bg);
    display: flex; flex-direction: column; align-items: center;
    padding-top: 120px; color: var(--text-light);
  }
  .brand-mark {
    width: 120px; height: 120px; border-radius: 50%;
    border: 9px solid var(--brand-blue);
  }
  .brand-name {
    margin-top: 18px;
    font-size: 50px; font-weight: 400; letter-spacing: 1px;
    color: var(--brand-blue);
    white-space: nowrap;
  }
  .person-name {
    margin-top: 56px;
    font-size: 26px; font-weight: 700; color: var(--brand-blue);
  }
  .person-title { margin-top: 4px; font-size: 20px; font-weight: 400; }
  .divider {
    display: flex; align-items: center; gap: 10px;
    width: 330px; margin-top: 20px;
  }
  .divider__line { flex: 1; height: 1px; background: var(--rule); }
  .divider__icons { display: flex; gap: 6px; }
  .icon-dot {
    width: 26px; height: 26px; border-radius: 50%;
    background: var(--brand-blue);
    display: flex; align-items: center; justify-content: center;
  }
  .icon-dot svg { width: 15px; height: 15px; }
  .contact-list {
    list-style: none; text-align: center; margin-top: 14px;
    font-size: 21px; line-height: 1.35;
  }
  .divider--location { margin-top: 18px; }
  .location { margin-top: 10px; font-size: 21px; }

  .card--back { background: var(--card-back-bg); }
  .back-pattern {
    position: absolute; inset: 0 0 200px 0;
    background: linear-gradient(180deg, var(--pattern-tone-a), var(--pattern-tone-b));
  }
  .back-wordmark {
    position: absolute; left: 46px; right: 46px; bottom: 84px;
    font-size: 46px; font-weight: 400; letter-spacing: 1px;
    color: var(--text-light);
    white-space: nowrap;
  }
</style>
</head>
<body>
<main class="canvas">
  <section class="card card--front">
    <div class="brand-mark"></div>
    <div class="brand-name">TALKHARBOR</div>
    <div class="person-name">MARCUS ELLERY</div>
    <div class="person-title">Managing Director</div>
    <div class="divider">
      <span class="divider__line"></span>
      <div class="divider__icons">
        <span class="icon-dot"><svg viewBox="0 0 16 16"><path fill="#1c1d1f" d="M4 1l3 3-2 2c1 2 3 4 5 5l2-2 3 3-2 2C7 14 2 9 1 3z"/></svg></span>
        <span class="icon-dot"><svg viewBox="0 0 16 16"><rect x="1" y="3" width="14" height="10" fill="#1c1d1f"/><path d="M1 3l7 6 7-6" fill="none" stroke="#1a9ad6" stroke-width="1.4"/></svg></span>
        <span class="icon-dot"><svg viewBox="0 0 16 16"><circle cx="8" cy="8" r="6.5" fill="none" stroke="#1c1d1f" stroke-width="1.5"/><ellipse cx="8" cy="8" rx="3" ry="6.5" fill="none" stroke="#1c1d1f" stroke-width="1.3"/><path d="M1.5 8h13" stroke="#1c1d1f" stroke-width="1.3"/></svg></span>
      </div>
      <span class="divider__line"></span>
    </div>
    <ul class="contact-list">
      <li>044 777 1234</li>
      <li>DaniaKV@talkharbor.co.uk</li>
      <li>www.TalkHarbor.co.uk</li>
    </ul>
    <div class="divider divider--location">
      <span class="divider__line"></span>
      <span class="icon-dot"><svg viewBox="0 0 16 16"><path fill="#1c1d1f" d="M8 1a5 5 0 0 0-5 5c0 4 5 9 5 9s5-5 5-9a5 5 0 0 0-5-5zm0 7a2 2 0 1 1 0-4 2 2 0 0 1 0 4z"/></svg></span>
      <span class="divider__line"></span>
    </div>
    <div class="location">London, UK</div>
  </section>

  <section class="card card--back">
    <div class="back-pattern" role="img" aria-label="Faint repeating brand emblem pattern"></div>
    <div class="back-wordmark">TALKHARBOR</div>
  </section>
</main>
</body>
</html>
```